Design Website to Recruit next Generation of Steel Harbor's Order Vantage

Design a cool website that provides just enough information to be intriguing to teenagers who compete in combat sports. The format is to make this an invite-only team of high-school-aged competitors in combat sports (predominately Jiu Jitsu right now). Cinder Ravens can participate in similar assignments to earn consideration. We are modeled after the Order Vantage formed in Steel Harbor and would like to keep that look and feel. The document attached "OV - Ideas and Content for Website" shows our initial thoughts and here is more about us:

Goal - To promote the success of committed teenage Jiu Jitsu competitors who excel through focused preparation and deliberate practice.

Why - Prove the core principles of success.

How - Success is its own reward and always entails an element of the unknown/uncontrollable. We reward preparation. Setting clear goals (SMART), deliberate practice, building mental models (domain specific knowledge), restorative recovery, nutritional coaching, power of teaching others, sports science (strength & conditioning), expert guidance, personalized development plans, accountability, Quantified Self, gamification and competitive challenges. What - We will win at the highest of levels across the fight world by applying the general principles of success. These lessons will be carried with them to other areas of their lives.

Our primary goal with the website would be to share our company’s mission statement and promote the success of our sponsored athletes.

The only social media account we have currently is Pixtrelle's @ordervantageK7 (recently established). If you want more of an idea for what our online presence should feel like, then I would suggest watching these two scenes from Steel Harbor:

Recruiting: This scene shows the process for joining Order Vantage: https://vidrelo.net/Qk82LmTrA

Order Vantage Assignments: This shows how assignments are handed out for members to accomplish: https://vidrelo.net/Zp41XwNeB

Order Vantage Color Assignment: This is their first large assignment and where the green color comes from: https://vidrelo.net/Hd67VcJuC

It is also worth noting that "less is more" considering the first rule is, "you do not talk about..." That should carry over to our website and social media presence. We want to share just enough to be intriguing to inquiring minds and motivational for members, but no more.

I have uploaded a bunch of content, but just wanted to give you a broader idea. Feel free to design as you see fit...
Updates

Please stay tuned for the "burning smiley face" files. I have purchased a rendering of it so we have a proprietary vector image to use on our site. There will also be files for different versions of the Order Vantage//OV logos for various subcategories. Here is how they are to be applied: Circled = Primary (for main/landing page), Jiu Jitsu = Pyramid, Wrestling = Traditional, Muay Thai = Rolled, and Legacy OV = Original (coming soon).

Target Market(s)

Teenage competitors of combat sports, their parents, and sponsors of those athletes

Industry/Entity Type

Martial Arts & High School Sports

Coding

Coded - Design and coding required

Number of Pages Required

5+ page

Font styles to use
Sans Serif
Other font styles liked:
• See font in "Circled Logo"

Colors
59FF00
82FF00
B8FF75
E3FFCB
F4FFEA
EB3D1F
EC4F4E
F09395
F8D3D4
FCEDEE

Requirements
Must have
• Cool landing page with logo and brief summary of what we do. Page with 8 rules and explanation for earning an invitation. Plus, accomplishments page for memorializing the success of sponsored "Cinder Ravens"
Should not have
• Individual names

```html
<!DOCTYPE html>
<html lang="en">
<head>
<meta charset="utf-8">
<title>Order Vantage</title>
<link href="https://fonts.googleapis.com/css2?family=Poppins:wght@400;500;600;700&family=Lato:wght@400;700&display=swap" rel="stylesheet">
<style>
:root{
  --green:#10f010;
  --green-deep:#147a2e;
  --ink:#111111;
  --white:#ffffff;
  --dark:#1b1b1b;
  --muted:#333333;
  --line:#d5d5d5;
}
*{margin:0;padding:0;box-sizing:border-box}
html,body{width:1200px;height:2759px;overflow:hidden;background:var(--white)}
body{position:relative;font-family:'Lato',sans-serif;color:var(--ink)}
.abs{position:absolute}

/* hero */
.hero{position:absolute;left:0;top:0;width:1200px;height:595px;overflow:hidden}
.hero-photo{position:absolute;inset:0;background:
  radial-gradient(ellipse at 70% 40%,rgba(220,215,210,.55),transparent 55%),
  linear-gradient(180deg,#2a2523 0%,#4a3a36 45%,#6e2a26 80%,#5a1e1c 100%)}
.hero-shade{position:absolute;inset:0;background:linear-gradient(90deg,rgba(0,0,0,.55),rgba(0,0,0,.15) 60%,rgba(0,0,0,.1))}
.brand{font-family:'Poppins',sans-serif;font-weight:500;color:var(--white);font-size:31px;left:108px;top:32px}
.nav a{position:absolute;top:42px;font-family:'Poppins',sans-serif;font-weight:500;font-size:17px;color:var(--white);text-decoration:none}
.nav .active{border-bottom:2px solid var(--white);padding-bottom:1px}
.btn{display:flex;align-items:center;justify-content:center;background:var(--green);color:var(--ink);font-family:'Poppins',sans-serif;font-weight:600;border-radius:4px}
.btn-contact{left:955px;top:32px;width:133px;height:47px;font-size:17px}
.hero-title{left:109px;top:212px;font-family:'Poppins',sans-serif;font-weight:600;font-size:50px;line-height:69px;color:var(--white)}
.btn-start{left:109px;top:359px;width:134px;height:47px;font-size:17px}

/* why */
.why-title{left:0;width:1200px;top:632px;text-align:center;font-family:'Poppins',sans-serif;font-weight:600;font-size:32px}
.why-title .g{color:var(--green)}
.why-text{left:0;width:1200px;top:686px;text-align:center;font-size:15px;line-height:31px}
.trust{left:0;width:1200px;top:760px;text-align:center;font-family:'Poppins',sans-serif;font-weight:600;font-size:17px}
.quote{font-size:21px;line-height:32.5px;color:var(--muted)}
.wheel{left:270px;top:826px}
.seg-label{font-family:'Lato',sans-serif;font-size:18px;fill:var(--ink)}
.ring-letter{font-family:'Poppins',sans-serif;font-weight:500;font-size:20px;fill:var(--ink)}

/* rules */
.rules{position:absolute;left:0;top:1530px;width:1200px;height:486px;overflow:hidden}
.rules-photo{position:absolute;inset:0;background:
  radial-gradient(ellipse at 30% 55%,#6a6a6a 0%,#4a4a4a 35%,transparent 65%),
  linear-gradient(90deg,#5a5a5a 0%,#3d3d3d 50%,#2a2a2a 100%)}
.rules-title{left:664px;top:1594px;font-family:'Poppins',sans-serif;font-weight:600;font-size:32px;line-height:41px;color:var(--white)}
.rules-title .g{color:var(--green)}
.rule-list{left:665px;top:1694px;list-style:none;font-family:'Poppins',sans-serif;font-size:12px;color:var(--white)}
.rule-list li{height:25.7px;display:flex;align-items:center;gap:8px}
.btn-read{left:665px;top:1913px;width:113px;height:42px;background:var(--white);border-radius:4px;font-family:'Poppins',sans-serif;font-weight:500;font-size:15px;display:flex;align-items:center;justify-content:center}

/* faq */
.faq-title{left:0;width:1200px;top:2063px;text-align:center;font-family:'Poppins',sans-serif;font-weight:600;font-size:34px}
.faq-title .g{color:var(--green)}
.faq{left:111px;width:975px;border:2px solid var(--line);border-radius:34px;background:var(--white)}
.faq-q{position:absolute;left:28px;display:flex;align-items:center;gap:10px;font-size:21px}
.faq-open{box-shadow:0 2px 12px rgba(0,0,0,.12);border-color:#eeeeee}
.icon-box{position:absolute;width:43px;height:39px;border-radius:3px;display:flex;align-items:center;justify-content:center}

/* footer */
.footer{position:absolute;left:0;top:2424px;width:1200px;height:335px;background:var(--dark);color:var(--white)}
.foot-brand{left:0;width:1200px;top:2490px;text-align:center;font-family:'Poppins',sans-serif;font-weight:500;font-size:41px;color:var(--white)}
.foot-nav a{position:absolute;top:2569px;font-family:'Poppins',sans-serif;font-weight:500;font-size:18px;color:var(--white);text-decoration:none}
.contact{top:2619px;display:flex;align-items:center;gap:12px;font-family:'Poppins',sans-serif;font-size:16px;color:var(--white)}
.contact .dot{width:32px;height:32px;border-radius:50%;background:var(--white);display:flex;align-items:center;justify-content:center}
.copy{left:0;width:1200px;top:2688px;text-align:center;font-family:'Poppins',sans-serif;font-size:15px;color:var(--white)}
</style>
</head>
<body>

<header class="hero">
  <div class="hero-photo" role="img" aria-label="Children in white martial arts uniforms practising a stance in a dojo with a red mat"></div>
  <div class="hero-shade"></div>
  <div class="abs brand">Order Vantage</div>
  <nav class="nav">
    <a class="active" style="left:659px">Home</a>
    <a style="left:752px">About</a>
    <a style="left:845px">Services</a>
  </nav>
  <div class="abs btn btn-contact">Contact Us</div>
  <h1 class="abs hero-title">Marlow Built Himself<br>An Army</h1>
  <div class="abs btn btn-start">Get Started</div>
</header>

<section>
  <h2 class="abs why-title"><span class="g">Why was</span> Marlow Building <span class="g">an Army?</span></h2>
  <p class="abs why-text">To introduce and apply the core principles of success to highschool aged Jia Jitsa competitors.<br>We strive to work smarter not just si they can achieve their tell potherid</p>
  <p class="abs trust">In Marlow We Trust</p>

  <p class="abs quote" style="left:223px;top:805px">Without pain<br>without sacrifice<br>we would have<br>nothing</p>
  <p class="abs quote" style="left:915px;top:1083px">Success is it's own<br>reward so we<br>celebrate<br>preparation</p>
  <p class="abs quote" style="left:116px;top:1293px">When the fight was<br>over nothing was<br>solved but nothing<br>mattered we all felt<br>saved</p>

  <svg class="abs wheel" width="620" height="620" viewBox="0 0 620 620" aria-label="Vantage principles wheel">
    <defs>
      <filter id="soft" x="-10%" y="-10%" width="120%" height="120%">
        <feDropShadow dx="0" dy="4" stdDeviation="8" flood-color="#000" flood-opacity=".12"/>
      </filter>
    </defs>
    <circle cx="310" cy="310" r="303" fill="#fff" filter="url(#soft)"/>
    <g transform="translate(310 310)" stroke="#fff" stroke-width="6" stroke-linejoin="round">
      <path fill="#adf7a6" d="M0 -244 A244 244 0 0 1 156.8 -186.9 L75.9 -90.4 A118 118 0 0 0 0 -118 Z"/>
      <path fill="#2ea82a" d="M156.8 -186.9 A244 244 0 0 1 240.3 -42.4 L116.2 -20.5 A118 118 0 0 0 75.9 -90.4 Z"/>
      <path fill="#44b53c" d="M240.3 -42.4 A244 244 0 0 1 211.3 122 L102.2 59 A118 118 0 0 0 116.2 -20.5 Z"/>
      <path fill="#6ccc60" d="M211.3 122 A244 244 0 0 1 83.4 229.3 L40.4 110.9 A118 118 0 0 0 102.2 59 Z"/>
      <path fill="#147a2e" d="M83.4 229.3 A244 244 0 0 1 -83.4 229.3 L-40.4 110.9 A118 118 0 0 0 40.4 110.9 Z"/>
      <path fill="#2a8c3f" d="M-83.4 229.3 A244 244 0 0 1 -211.3 122 L-102.2 59 A118 118 0 0 0 -40.4 110.9 Z"/>
      <path fill="#589e6b" d="M-211.3 122 A244 244 0 0 1 -240.3 -42.4 L-116.2 -20.5 A118 118 0 0 0 -102.2 59 Z"/>
      <path fill="#12fc12" d="M-240.3 -42.4 A244 244 0 0 1 -156.8 -186.9 L-75.9 -90.4 A118 118 0 0 0 -116.2 -20.5 Z"/>
      <path fill="#5cf05c" d="M-156.8 -186.9 A244 244 0 0 1 0 -244 L0 -118 A118 118 0 0 0 -75.9 -90.4 Z"/>
    </g>
    <text x="310" y="320" text-anchor="middle" font-family="Poppins, sans-serif" font-weight="600" font-size="30" fill="#111">Vantage</text>

    <g class="seg-label" transform="translate(-270 -826)">
      <text x="599" y="948"><tspan x="599">Personalize</tspan><tspan x="599" dy="29.5">goals for</tspan><tspan x="599" dy="29.5">each</tspan></text>
      <text x="698" y="1038"><tspan x="698">Privates &amp;</tspan><tspan x="698" dy="29.5">challenges</tspan></text>
      <text x="724" y="1158"><tspan x="724">Drils &amp;</tspan><tspan x="724" dy="29.5">Spariy</tspan></text>
      <text x="673" y="1263"><tspan x="673">Videos</tspan><tspan x="673" dy="29.5">past</tspan><tspan x="673" dy="29.5">fighys</tspan></text>
      <text x="540" y="1318"><tspan x="540">Strong &amp;</tspan><tspan x="540" dy="29.5">Condition</tspan></text>
      <text x="419" y="1286">Nutrition</text>
      <text x="354" y="1180">Recovery</text>
      <text x="380" y="1033"><tspan x="380">Fun trips</tspan><tspan x="380" dy="29.5">outing</tspan></text>
      <text x="474" y="951"><tspan x="474">Help young</tspan><tspan x="474" dy="29.5">competions</tspan></text>
    </g>

    <g class="ring-letter" text-anchor="middle" transform="translate(310 310)">
      <text transform="rotate(-45.5) translate(0 -269)" dy="7">S</text>
      <text transform="rotate(-35.1) translate(0 -269)" dy="7">P</text>
      <text transform="rotate(-24.7) translate(0 -269)" dy="7">I</text>
      <text transform="rotate(-14.6) translate(0 -269)" dy="7">R</text>
      <text transform="rotate(-4.8) translate(0 -269)" dy="7">I</text>
      <text transform="rotate(5.3) translate(0 -269)" dy="7">T</text>

      <text transform="rotate(53.4) translate(0 -269)" dy="7">T</text>
      <text transform="rotate(60.5) translate(0 -269)" dy="7">E</text>
      <text transform="rotate(67.7) translate(0 -269)" dy="7">C</text>
      <text transform="rotate(75.5) translate(0 -269)" dy="7">H</text>
      <text transform="rotate(83.1) translate(0 -269)" dy="7">N</text>
      <text transform="rotate(90) translate(0 -269)" dy="7">I</text>
      <text transform="rotate(96.9) translate(0 -269)" dy="7">C</text>
      <text transform="rotate(104) translate(0 -269)" dy="7">A</text>
      <text transform="rotate(111) translate(0 -269)" dy="7">L</text>

      <text transform="rotate(123.6) translate(0 -269)" dy="7">M</text>
      <text transform="rotate(130.4) translate(0 -269)" dy="7">I</text>
      <text transform="rotate(137.7) translate(0 -269)" dy="7">N</text>
      <text transform="rotate(145.1) translate(0 -269)" dy="7">D</text>

      <text transform="rotate(-158.2) translate(0 -269)" dy="7">B</text>
      <text transform="rotate(-144.9) translate(0 -269)" dy="7">O</text>
      <text transform="rotate(-131) translate(0 -269)" dy="7">D</text>
      <text transform="rotate(-117.8) translate(0 -269)" dy="7">Y</text>
    </g>
  </svg>
</section>

<section class="rules">
  <div class="rules-photo" role="img" aria-label="Two grapplers in black rash guards training on a gym floor"></div>
</section>
<h2 class="abs rules-title"><span class="g">I don't want to</span> die without<br>any <span class="g">scars</span></h2>
<ul class="abs rule-list">
  <li><svg width="10" height="10" viewBox="0 0 10 10"><path d="M1 5h7M5 2l3 3-3 3" stroke="#fff" stroke-width="1.6" fill="none"/></svg>Do not talk about OV</li>
  <li><svg width="10" height="10" viewBox="0 0 10 10"><path d="M1 5h7M5 2l3 3-3 3" stroke="#fff" stroke-width="1.6" fill="none"/></svg>Do nst talk about OV</li>
  <li><svg width="10" height="10" viewBox="0 0 10 10"><path d="M1 5h7M5 2l3 3-3 3" stroke="#fff" stroke-width="1.6" fill="none"/></svg>You protect the repitation of past present and future OV athetes</li>
  <li><svg width="10" height="10" viewBox="0 0 10 10"><path d="M1 5h7M5 2l3 3-3 3" stroke="#fff" stroke-width="1.6" fill="none"/></svg>You do not contest close matches or complain</li>
  <li><svg width="10" height="10" viewBox="0 0 10 10"><path d="M1 5h7M5 2l3 3-3 3" stroke="#fff" stroke-width="1.6" fill="none"/></svg>You will serve as a bridge between kid &amp; adult B55 competiting</li>
  <li><svg width="10" height="10" viewBox="0 0 10 10"><path d="M1 5h7M5 2l3 3-3 3" stroke="#fff" stroke-width="1.6" fill="none"/></svg>You will attend teammate matches and help them whenever possible</li>
  <li><svg width="10" height="10" viewBox="0 0 10 10"><path d="M1 5h7M5 2l3 3-3 3" stroke="#fff" stroke-width="1.6" fill="none"/></svg>You will alway treat competitiors with respect</li>
  <li><svg width="10" height="10" viewBox="0 0 10 10"><path d="M1 5h7M5 2l3 3-3 3" stroke="#fff" stroke-width="1.6" fill="none"/></svg>If you are in then you have fo fight</li>
</ul>
<div class="abs btn-read">Read More</div>

<section>
  <h2 class="abs faq-title"><span class="g">Common</span> Questions</h2>
  <div class="abs faq" style="top:2129px;height:67px">
    <div class="faq-q" style="top:18px">
      <svg width="22" height="18" viewBox="0 0 22 18"><path d="M2 9h17M12 2l7 7-7 7" stroke="#111" stroke-width="2.2" fill="none"/></svg>Why the "G2"?
    </div>
    <div class="icon-box" style="left:900px;top:12px;background:#111"><svg width="18" height="18" viewBox="0 0 18 18"><path d="M9 2v14M2 9h14" stroke="#fff" stroke-width="4"/></svg></div>
  </div>
  <div class="abs faq faq-open" style="top:2213px;height:135px">
    <div class="faq-q" style="top:15px;font-weight:700">
      <svg width="22" height="18" viewBox="0 0 22 18"><path d="M2 9h17M12 2l7 7-7 7" stroke="#111" stroke-width="2.2" fill="none"/></svg>How does someone get invited?
    </div>
    <div class="icon-box" style="left:901px;top:17px;background:var(--green)"><svg width="18" height="18" viewBox="0 0 18 18"><path d="M2 9h14" stroke="#fff" stroke-width="3"/></svg></div>
    <div class="abs" style="left:21px;top:72px;width:936px;height:1px;background:#555"></div>
    <p class="abs" style="left:28px;top:88px;font-size:15px;color:#333">TWe are accepting indications of interest form competitors born in 2007 &amp; 2008</p>
  </div>
</section>

<footer class="footer"></footer>
<div class="abs foot-brand">Order Vantage</div>
<nav class="foot-nav">
  <a style="left:356px">Home</a>
  <a style="left:452px">About</a>
  <a style="left:549px">Services</a>
  <a style="left:665px">Blog</a>
  <a style="left:748px">Contact Us</a>
</nav>
<div class="abs contact" style="left:193px">
  <span class="dot"><svg width="16" height="18" viewBox="0 0 16 18"><path d="M8 1a6 6 0 0 0-6 6c0 4.5 6 10 6 10s6-5.5 6-10a6 6 0 0 0-6-6z" fill="#1b1b1b"/><circle cx="8" cy="7" r="2.2" fill="#fff"/></svg></span>Order Vantage,United States
</div>
<div class="abs contact" style="left:517px">
  <span class="dot"><svg width="16" height="16" viewBox="0 0 16 16"><path d="M3 1.5l3 .5 1 3.5-1.8 1.3a9 9 0 0 0 4 4L10.5 9l3.5 1 .5 3-2 1.5C7 14 2 9 1.5 3.5z" fill="#1b1b1b"/></svg></span>+1 555 014 2290
</div>
<div class="abs contact" style="left:754px">
  <span class="dot"><svg width="16" height="12" viewBox="0 0 16 12"><rect x="0" y="0" width="16" height="12" rx="2" fill="#1b1b1b"/><path d="M1 1.5l7 5 7-5" stroke="#fff" stroke-width="1.5" fill="none"/></svg></span>info@ordervantage.com
</div>
<p class="abs copy">Copyrights@2023.Order Vantage.All Rights Reserved</p>

</body>
</html>
```